Business cards to launch an education platform

Hi,
I am looking at having new business cards designed.
I am a startup, developing a web platform for schools and university, the education world. It's an online assessment system.
I would like a card that looks classy, and that is using the colors and the font of my logo.

I have attached:
1) my logo
2) A business card that I have designed quickly so you can have all the information required in the card, but I really don't like it.
3) The font that I am using (Lato Regular) to design my web platform
4) Some screenshots of my web platform so you can have a look at the style that I have.

Target Market(s)

Major market: Education system: Schools and university
Minor markets: Business in general

Industry/Entity Type

Business

Contact Information for Business Card

Clara Fenwick
Director

M: 0437 518 902
E: clara.fenwick@amberLoomSystems.com.au

Requirements
Must have
• The colors of my logo

```html
<!DOCTYPE html>
<html lang="en">
<head>
<meta charset="utf-8">
<title>Amber Loom Systems – Business Cards</title>
<link href="https://fonts.googleapis.com/css2?family=Lato:wght@400;700&display=swap" rel="stylesheet">
<style>
  :root {
    --page-bg: #e9edf2;
    --deep-blue: #0a5ea8;
    --mid-blue: #1a75c0;
    --bright-blue: #3a9fdc;
    --navy: #1b3f73;
    --cyan: #29abe2;
    --stripe: #5ec8dc;
    --white: #ffffff;
  }
  * { margin: 0; padding: 0; box-sizing: border-box; }
  html, body {
    width: 1189px;
    height: 1200px;
    overflow: hidden;
    background: var(--page-bg);
    font-family: "Lato", sans-serif;
  }
  .card-slot {
    position: absolute;
    left: 112px;
    width: 964px;
    height: 549px;
    box-shadow: 0 6px 16px rgba(0,0,0,0.18);
  }
  .card-slot--front { top: 34px; }
  .card-slot--back { top: 617px; }
  .card {
    position: absolute;
    top: 0; left: 0;
    width: 1048px;
    height: 597px;
    transform: scale(0.9198);
    transform-origin: top left;
    overflow: hidden;
  }

  /* Front */
  .card--front {
    background: radial-gradient(ellipse at 50% 42%, var(--bright-blue) 0%, var(--mid-blue) 45%, var(--deep-blue) 100%);
    display: flex;
    align-items: center;
    justify-content: center;
  }
  .wordmark {
    display: flex;
    align-items: center;
    gap: 30px;
  }
  .wordmark__square {
    width: 120px;
    height: 120px;
  }
  .wordmark__name {
    font-weight: 400;
    line-height: 1.05;
  }
  .wordmark__line1 { display: block; font-size: 62px; letter-spacing: 6px; }
  .wordmark__line2 { display: block; font-size: 44px; letter-spacing: 6px; }
  .card--front .wordmark__square { background: var(--white); }
  .card--front .wordmark__name { color: var(--white); }

  /* Back */
  .card--back { background: var(--white); }
  .swoosh { position: absolute; inset: 0; width: 1048px; height: 597px; }
  .card--back .wordmark {
    position: absolute;
    left: 65px;
    top: 100px;
    gap: 26px;
  }
  .card--back .wordmark__square { background: var(--mid-blue); width: 130px; height: 130px; }
  .card--back .wordmark__name { color: var(--navy); }

  .person {
    position: absolute;
    left: 65px;
    top: 345px;
  }
  .person__name {
    font-weight: 700;
    font-size: 40px;
    color: var(--navy);
    line-height: 1.05;
  }
  .person__role {
    font-size: 27px;
    color: var(--cyan);
    line-height: 1.1;
  }
  .contacts {
    position: absolute;
    left: 65px;
    top: 460px;
    list-style: none;
  }
  .contacts__item {
    display: flex;
    align-items: center;
    gap: 12px;
    font-size: 27px;
    color: var(--navy);
    height: 36px;
  }
  .contacts__icon { width: 30px; height: 28px; flex: none; }
</style>
</head>
<body>

<div class="card-slot card-slot--front">
  <section class="card card--front">
    <div class="wordmark">
      <span class="wordmark__square"></span>
      <span class="wordmark__name">
        <span class="wordmark__line1">AMBER LOOM</span>
        <span class="wordmark__line2">Systems</span>
      </span>
    </div>
  </section>
</div>

<div class="card-slot card-slot--back">
  <section class="card card--back">
    <svg class="swoosh" viewBox="0 0 1048 597" aria-hidden="true">
      <defs>
        <linearGradient id="swooshBlue" x1="0" y1="0" x2="1" y2="0">
          <stop offset="0" stop-color="#2aa3e0"/>
          <stop offset="0.55" stop-color="#1a78c2"/>
          <stop offset="1" stop-color="#0a5ea8"/>
        </linearGradient>
      </defs>
      <path d="M440,0 C690,15 950,170 945,340 C940,460 835,555 758,597 L750,597 C820,555 920,460 925,340 C930,150 640,5 330,0 Z" fill="var(--stripe)"/>
      <path d="M650,0 C900,70 985,200 965,340 C950,450 860,550 770,597 L1048,597 L1048,0 Z" fill="url(#swooshBlue)"/>
    </svg>

    <div class="wordmark">
      <span class="wordmark__square"></span>
      <span class="wordmark__name">
        <span class="wordmark__line1">AMBER LOOM</span>
        <span class="wordmark__line2">Systems</span>
      </span>
    </div>

    <div class="person">
      <p class="person__name">Clara Fenwick</p>
      <p class="person__role">Director</p>
    </div>

    <ul class="contacts">
      <li class="contacts__item">
        <svg class="contacts__icon" viewBox="0 0 30 28" aria-hidden="true">
          <rect width="30" height="28" fill="var(--mid-blue)"/>
          <rect x="10" y="4" width="10" height="20" rx="2" fill="none" stroke="#fff" stroke-width="1.6"/>
          <rect x="12" y="7" width="6" height="6" fill="#fff"/>
          <circle cx="15" cy="19" r="1.4" fill="#fff"/>
        </svg>
        <span>0437 518 902</span>
      </li>
      <li class="contacts__item">
        <svg class="contacts__icon" viewBox="0 0 30 28" aria-hidden="true">
          <rect width="30" height="28" fill="var(--mid-blue)"/>
          <rect x="6" y="8" width="18" height="13" fill="none" stroke="#fff" stroke-width="1.6"/>
          <path d="M6,8 L15,16 L24,8 M6,21 L12,14 M24,21 L18,14" fill="none" stroke="#fff" stroke-width="1.4"/>
        </svg>
        <span>clara.fenwick@amberLoomSystems.com.au</span>
      </li>
    </ul>
  </section>
</div>

</body>
</html>
```